Velvet Table

A quick run down of the iPhone app and what it does:

1. It has a home screen for that restaurant that will guide you to the menu.
2. You can search the menu which has all the pictures of the items on the menu.
3. There are also ratings from the users on each item.
4. You can also order and pay from the app.

Please see this link to look at the wire-frame we have created (Click on the buttons to move from page to page)
https://www.plandraft.example/editor/live/preview/p_4KdmTrwQzLpxeNvBcHyUaJ2PQ8xwrt5m.2738491026374

We would like something that is very clean, minimalist and uses modern design to convey the feeling of cultured.

I would like the designer to create at least 5 pages:

1. The Home screen to the restaurant. (call it Harbor Plate) You can redo the buttons to make it look better. Like have a logo or something better than box buttons. Please use good looking easy to read fonts, Modern you might say.

2. and 3. The Menu page with 3 items and pictures per menu title like Appetizers and Entrees have it look as if it is dropping down (you can use your own photos or some from the web with descriptions like what you see on the Wire-frame)

4. The item drill down, as you click on an item from the menu it comes up with a larger photo of the item and the description and also the rating under the description. (see wire-frame)

5. The order page with items from the menu on the order page with prices.

I would like for the bottom menu to be updated with some nice looking buttons. For one the help now button I would like to have a circle with an outline of a person raising their hand.

I currently don't have a logo or photos so I will rely on your discretion to find the photos you need. I also have no particular colors in mind but here are some app designs I really like.

http://gallery-mocks.example/tagged/app_velo#show-all

http://31.media.picshelf.example/4a9c27e0b3d15f86ac024e7b91d3f6c2/pics_k4tzbqweLM2s83kpq2_400.png (put the item name on this and a plus sign in the top right of the photo)

http://37.media.picshelf.example/b71e05ac9d24f3e8c6a1570d2fe9b8c4/pics_k4tz7rvhQW9s83kpq2_400.png ( take out all the words and put in all the information I have on the page with the large picture, from my wire-frame, the drill down page)

If you follow the same sort of app design with a photo in the background of the restaurant home page and clear design like this you will for sure win.

Also after this is done I will most likely have the winning designer create my logo, and app icon.

Target Market(s)

The target market of this App are people that can afford to eat out and enjoy using technology to have a better dining experience. Ages 16 to 45 Male and Female.

Industry/Entity Type

Restaurant

Font styles to use
Sans Serif

Requirements
Must have
• Clear, high quality photos, I don't want to see any individual pixels. Please read my outline carefully to understand what this app will do.
Nice to have
• I want to feel like I'm having a good experience from the moment I open the app the the moment I finish my meal with the app. Come up with something simple and creative for the user to experience while dining.
Should not have
• Please do not just submit my wire-frame in different colors that will be a waste of your time and mine. I don't want to see boxes as the buttons.

```html
<!DOCTYPE html>
<html lang="en">
<head>
<meta charset="utf-8">
<title>Velvet Table – Harbor Plate app screens</title>
<link href="https://fonts.googleapis.com/css2?family=Lato:wght@400;700;900&display=swap" rel="stylesheet">
<style>
:root{
  --stage:#343234;
  --accent-a:#f3404c;
  --accent-b:#ff4a10;
  --accent:#f7453a;
  --body:#d9dadd;
  --row-line:#b9bbbf;
  --ink:#4a4a4e;
  --panel:#3f4657;
  --pill-grey:#6b6b6e;
  --white:#ffffff;
}
*{box-sizing:border-box;margin:0;padding:0}
html,body{width:1024px;height:1200px;overflow:hidden;background:var(--stage)}
body{font-family:'Lato',sans-serif}
.board{position:absolute;left:0;top:0;width:1256px;height:1472px;transform:scale(.8153);transform-origin:0 0}
.screen{position:absolute;width:320px;background:var(--body);display:flex;flex-direction:column;overflow:hidden}
.bar{background:linear-gradient(90deg,var(--accent-a),var(--accent-b));color:var(--white)}
.status{height:33px;position:relative;font-size:14px;display:flex;align-items:center;justify-content:center}
.status .signal{position:absolute;left:12px;top:11px}
.status .battery{position:absolute;right:12px;top:12px}
.nav{height:40px;display:flex;align-items:center;padding-left:12px}
.nav .back{font-size:15px;display:flex;align-items:center;gap:6px;width:68px}
.nav .title{font-weight:900;font-size:19px;letter-spacing:.2px}
.tabbar{height:72px;display:flex;font-size:13px}
.tab{flex:1;display:flex;flex-direction:column;align-items:center;justify-content:center;gap:6px}
.foot{height:11px;background:var(--body)}
.menu-list .row{height:48px;border-bottom:1px solid var(--row-line);display:flex;align-items:center;justify-content:space-between;padding:0 22px 0 25px;color:#555;font-size:14px}
.spacer{flex:1}
.home-photo{position:absolute;left:0;top:73px;width:320px;height:417px;background:linear-gradient(180deg,#3a2a26 0%,#6b4632 35%,#a8703f 62%,#d9dadd 100%)}
.pill{position:absolute;height:32px;border-radius:16px;color:var(--white);font-size:13px;display:flex;align-items:center;justify-content:center}
.pill.grey{background:var(--pill-grey)}
.pill.hot{background:linear-gradient(90deg,var(--accent-a),var(--accent-b))}
.section-head{color:var(--accent);font-size:17px;padding-left:13px;height:42px;display:flex;align-items:center}
.dish{height:89px;background:var(--panel);display:flex;margin-bottom:12px;position:relative}
.dish:last-of-type{margin-bottom:8px}
.counter{width:28px;background:var(--accent-b);display:flex;flex-direction:column;align-items:center;justify-content:space-between;padding:10px 0;color:var(--white);font-size:15px}
.photo{background:radial-gradient(circle at 55% 45%,#d6901e 0,#a9631a 35%,#5a3a26 70%,#2b2a30 100%)}
.dish .photo{width:93px}
.dish .info{flex:1;color:var(--white);padding:6px 13px 0 10px}
.dish .name{display:flex;justify-content:space-between;font-size:13px;margin-bottom:4px}
.dish .desc{font-size:9.5px;line-height:14px;text-align:justify}
.cat-row{height:43px;border-bottom:1px solid var(--row-line);display:flex;align-items:center;padding-left:13px;color:#555;font-size:16px}
.hero{position:absolute;left:28px;top:131px;width:277px;height:261px;border-radius:8px;background:radial-gradient(circle at 50% 50%,#f5d63a 0,#e8b93c 18%,#e9c98c 30%,#cfa560 55%,#5a1510 85%,#3d0a08 100%)}
.side-counter{position:absolute;left:-1px;top:217px;width:28px;height:88px}
.detail-band{position:absolute;left:0;top:422px;width:320px;height:70px;background:linear-gradient(90deg,var(--accent-a),var(--accent-b));color:var(--white);padding:7px 13px}
.detail-band h3{font-weight:400;font-size:18px}
.detail-band p{font-size:9.5px;line-height:14px;margin-top:4px;text-align:justify}
.review{position:absolute;left:0;top:499px;width:320px;height:92px;background:linear-gradient(#d2d3d5,#b7b8bb);padding:8px 13px;font-size:11.5px;color:#444}
.review .overall{text-align:right;color:var(--accent-b);font-size:10px;font-weight:700;display:flex;justify-content:flex-end;align-items:center;gap:3px}
.review .who{font-size:10px;font-weight:700;display:flex;align-items:center;gap:3px;margin-top:-2px;color:#222}
.review p{margin-top:10px;line-height:14px;text-align:justify}
.order-table{position:absolute;left:0;top:84px;width:320px;height:179px;background:var(--panel);color:var(--white);font-size:13px;padding-top:8px}
.order-table .line{display:grid;grid-template-columns:112px 46px 54px auto;padding-left:14px;height:39px;align-items:center}
.submit{position:absolute;left:0;top:263px;width:320px;height:35px;display:flex;align-items:center;justify-content:center;font-size:13px}
</style>
</head>
<body>
<svg width="0" height="0" style="position:absolute">
  <defs>
    <g id="signal"><rect x="0" y="7" width="2.5" height="4" fill="#fff"/><rect x="3.5" y="5" width="2.5" height="6" fill="#fff"/><rect x="7" y="2.5" width="2.5" height="8.5" fill="#fff"/><rect x="10.5" y="0" width="2.5" height="11" fill="#fff"/></g>
    <g id="battery"><rect x=".5" y=".5" width="19" height="8" rx="1.5" fill="none" stroke="#fff"/><rect x="2" y="2" width="16" height="5" fill="#fff"/><rect x="20" y="3" width="1.5" height="3" fill="#fff"/></g>
    <g id="chev"><path d="M6 1 1 6l5 5" fill="none" stroke="#fff" stroke-width="2.2"/></g>
    <g id="ico-order"><rect x="1" y="3" width="9" height="9" fill="none" stroke="#fff" stroke-width="1.2"/><path d="M5 8l7-7 1.5 1.5-7 7H5z" fill="#fff"/></g>
    <g id="ico-help"><path d="M7 0 14 12H0z" fill="#fff"/><rect x="6.3" y="4" width="1.4" height="4.5" fill="#e84"/><rect x="6.3" y="9.4" width="1.4" height="1.4" fill="#e84"/></g>
    <g id="ico-table"><rect x=".5" y=".5" width="12" height="10" fill="none" stroke="#fff"/><path d="M.5 4h12M.5 7.3h12M4.5.5v10M8.5.5v10" stroke="#fff"/></g>
    <g id="ico-menu"><rect x=".5" y=".5" width="12" height="10" fill="none" stroke="#fff" stroke-width="1.2"/><path d="M6.5.5v10" stroke="#fff" stroke-width="1.2"/></g>
    <g id="arrow"><path d="M0 5h12M8 1.5 12 5 8 8.5" fill="none" stroke="#555" stroke-width="1.6"/></g>
    <g id="plus"><rect width="15" height="15" rx="3" fill="#fff"/><path d="M7.5 3.5v8M3.5 7.5h8" stroke="#ff4a10" stroke-width="2.2"/></g>
    <g id="minus"><rect width="15" height="15" rx="3" fill="#fff"/><path d="M3.5 7.5h8" stroke="#ff4a10" stroke-width="2.2"/></g>
    <g id="star-o"><path d="M6 .5l1.6 3.6 3.9.4-2.9 2.6.9 3.9L6 9 2.5 11l.9-3.9L.5 4.5l3.9-.4z" fill="none" stroke="#333" stroke-width=".9"/></g>
    <g id="star-f"><path d="M6 .5l1.6 3.6 3.9.4-2.9 2.6.9 3.9L6 9 2.5 11l.9-3.9L.5 4.5l3.9-.4z" fill="#ff4a10"/></g>
  </defs>
</svg>

<div class="board">

  <!-- Categories -->
  <section class="screen" style="left:64px;top:85px;height:573px">
    <header class="bar">
      <div class="status"><svg class="signal" width="14" height="11"><use href="#signal"/></svg>4:52 AM<svg class="battery" width="22" height="9"><use href="#battery"/></svg></div>
      <div class="nav"><span class="back"><svg width="8" height="12"><use href="#chev"/></svg>Back</span><span class="title">Harbor Plate</span></div>
    </header>
    <nav class="menu-list" style="margin-top:3px">
      <div class="row">Drinks<svg width="13" height="10"><use href="#arrow"/></svg></div>
      <div class="row">Appetizers<svg width="13" height="10"><use href="#arrow"/></svg></div>
      <div class="row">Pasta<svg width="13" height="10"><use href="#arrow"/></svg></div>
      <div class="row">Entrees<svg width="13" height="10"><use href="#arrow"/></svg></div>
      <div class="row">Salad<svg width="13" height="10"><use href="#arrow"/></svg></div>
      <div class="row">Burgers<svg width="13" height="10"><use href="#arrow"/></svg></div>
      <div class="row">Dessert<svg width="13" height="10"><use href="#arrow"/></svg></div>
    </nav>
    <div class="spacer"></div>
    <footer class="tabbar bar">
      <div class="tab"><svg width="14" height="13"><use href="#ico-order"/></svg>Order</div>
      <div class="tab"><svg width="14" height="12"><use href="#ico-help"/></svg>Help now</div>
      <div class="tab"><svg width="13" height="11"><use href="#ico-table"/></svg>Table</div>
      <div class="tab"><svg width="13" height="11"><use href="#ico-menu"/></svg>Menu</div>
    </footer>
    <div class="foot"></div>
  </section>

  <!-- Home -->
  <section class="screen" style="left:434px;top:89px;height:573px">
    <header class="bar">
      <div class="status"><svg class="signal" width="14" height="11"><use href="#signal"/></svg>4:52 AM<svg class="battery" width="22" height="9"><use href="#battery"/></svg></div>
      <div class="nav"><span class="back"><svg width="8" height="12"><use href="#chev"/></svg>Back</span><span class="title">Harbor Plate</span></div>
    </header>
    <div class="home-photo" role="img" aria-label="Photo of the Harbor Plate dining room in warm evening light"></div>
    <div class="pill grey" style="left:37px;top:400px;width:110px">Menu</div>
    <div class="pill grey" style="left:168px;top:400px;width:110px">Tastely Ratings</div>
    <div class="pill hot" style="left:37px;top:443px;width:245px">Submit Review</div>
    <div class="spacer"></div>
    <footer class="tabbar bar">
      <div class="tab"><svg width="14" height="13"><use href="#ico-order"/></svg>Order</div>
      <div class="tab"><svg width="14" height="12"><use href="#ico-help"/></svg>Help now</div>
      <div class="tab"><svg width="13" height="11"><use href="#ico-table"/></svg>Table</div>
      <div class="tab"><svg width="13" height="11"><use href="#ico-menu"/></svg>Menu</div>
    </footer>
    <div class="foot"></div>
  </section>

  <!-- Menu drop-down -->
  <section class="screen" style="left:795px;top:80px;height:685px">
    <header class="bar">
      <div class="status"><svg class="signal" width="14" height="11"><use href="#signal"/></svg>4:52 AM<svg class="battery" width="22" height="9"><use href="#battery"/></svg></div>
      <div class="nav"><span class="back"><svg width="8" height="12"><use href="#chev"/></svg>Back</span><span class="title">Harbor Plate</span></div>
    </header>
    <div class="section-head">Appetizers</div>
    <article class="dish">
      <div class="counter"><svg width="15" height="15"><use href="#plus"/></svg>1<svg width="15" height="15"><use href="#minus"/></svg></div>
      <div class="photo" role="img" aria-label="Photo of mozzarella sticks with marinara"></div>
      <div class="info"><div class="name"><span>Mozzaralla sticks</span><span>3.99</span></div>
      <p class="desc">Warm, melty mozzarella cheese covered in italian ad crumbs and fried to a crispy golden brown. Perfect dipping in marinara sauce</p></div>
    </article>
    <article class="dish">
      <div class="counter"><svg width="15" height="15"><use href="#plus"/></svg>0<svg width="15" height="15"><use href="#minus"/></svg></div>
      <div class="photo" role="img" aria-label="Photo of chips and queso"></div>
      <div class="info"><div class="name"><span>Chips and Queso</span><span>5.98</span></div>
      <p class="desc">Cheese dip with seasoned beef. served with warm tostchips and our house made salsa</p></div>
    </article>
    <article class="dish">
      <div class="counter"><svg width="15" height="15"><use href="#plus"/></svg>0<svg width="15" height="15"><use href="#minus"/></svg></div>
      <div class="photo" role="img" aria-label="Photo of Texas cheese fries"></div>
      <div class="info"><div class="name"><span>Texas Cheese Fries</span><span>5.98</span></div>
      <p class="desc">With applewood smoked bacon, jalapenos and green onion. served with rach dressing.</p></div>
    </article>
    <div class="cat-row" style="border-top:1px solid var(--row-line)">Pasta</div>
    <div class="cat-row">Entrees</div>
    <div class="cat-row">Salad</div>
    <div class="cat-row" style="border-bottom:none">Pasta</div>
    <div class="spacer"></div>
    <footer class="tabbar bar">
      <div class="tab"><svg width="14" height="13"><use href="#ico-order"/></svg>Order</div>
      <div class="tab"><svg width="14" height="12"><use href="#ico-help"/></svg>Help now</div>
      <div class="tab"><svg width="13" height="11"><use href="#ico-table"/></svg>Table</div>
      <div class="tab"><svg width="13" height="11"><use href="#ico-menu"/></svg>Menu</div>
    </footer>
    <div class="foot"></div>
  </section>

  <!-- Item detail -->
  <section class="screen" style="left:65px;top:741px;height:695px">
    <header class="bar">
      <div class="status"><svg class="signal" width="14" height="11"><use href="#signal"/></svg>4:52 AM<svg class="battery" width="22" height="9"><use href="#battery"/></svg></div>
      <div class="nav"><span class="back"><svg width="8" height="12"><use href="#chev"/></svg>Back</span><span class="title">Harbor Plate</span></div>
    </header>
    <div class="section-head" style="height:48px">Appetizers</div>
    <div class="hero" role="img" aria-label="Large photo of chips and queso with jalapenos"></div>
    <div class="counter side-counter"><svg width="15" height="15"><use href="#plus"/></svg>0<svg width="15" height="15"><use href="#minus"/></svg></div>
    <div class="detail-band"><h3>Chips and Queso</h3><p>Cheese dip seasoned beef. served with warm tostada chips and our house-made salsa</p></div>
    <div class="review">
      <div class="overall">OVERALL <svg width="12" height="12"><use href="#star-o"/></svg><svg width="12" height="12"><use href="#star-f"/></svg><svg width="12" height="12"><use href="#star-o"/></svg></div>
      <div class="who">R. Calder <svg width="12" height="12"><use href="#star-o"/></svg><svg width="12" height="12"><use href="#star-f"/></svg><svg width="12" height="12"><use href="#star-f"/></svg></div>
      <p>These went so fast with all grand children eating them i wish they would have more on the plate.</p>
    </div>
    <div class="spacer"></div>
    <footer class="tabbar bar">
      <div class="tab"><svg width="14" height="13"><use href="#ico-order"/></svg>Order</div>
      <div class="tab"><svg width="14" height="12"><use href="#ico-help"/></svg>Help now</div>
      <div class="tab"><svg width="13" height="11"><use href="#ico-table"/></svg>Table</div>
      <div class="tab"><svg width="13" height="11"><use href="#ico-menu"/></svg>Menu</div>
    </footer>
    <div class="foot" style="height:23px"></div>
  </section>

  <!-- Order -->
  <section class="screen" style="left:434px;top:760px;height:572px">
    <header class="bar">
      <div class="status"><svg class="signal" width="14" height="11"><use href="#signal"/></svg>4:52 AM<svg class="battery" width="22" height="9"><use href="#battery"/></svg></div>
      <div class="nav"><span class="back"><svg width="8" height="12"><use href="#chev"/></svg>Back</span><span class="title">Harbor Plate</span></div>
    </header>
    <div class="order-table">
      <div class="line"><span>Citrus Spritz</span><span>x2</span><span>5.50</span><span>Review Item</span></div>
      <div class="line"><span>Dark Cherry</span><span>x1</span><span>2.75</span><span>Review Item</span></div>
      <div class="line"><span>Mozzarella Sticks</span><span>x2</span><span>5.50</span><span>Review Item</span></div>
      <div class="line"><span>Cheese</span><span>x1</span><span>5.50</span><span>Review Item</span></div>
    </div>
    <div class="submit bar">SUBMIT ORDER</div>
    <div class="pill hot" style="left:37px;top:400px;width:110px">Review</div>
    <div class="pill hot" style="left:168px;top:400px;width:110px">Note for waiter</div>
    <div class="pill hot" style="left:37px;top:443px;width:245px">Pay Now</div>
    <div class="spacer"></div>
    <footer class="tabbar bar">
      <div class="tab"><svg width="14" height="13"><use href="#ico-order"/></svg>Order</div>
      <div class="tab"><svg width="14" height="12"><use href="#ico-help"/></svg>Help now</div>
      <div class="tab"><svg width="13" height="11"><use href="#ico-table"/></svg>Table</div>
      <div class="tab"><svg width="13" height="11"><use href="#ico-menu"/></svg>Menu</div>
    </footer>
    <div class="foot" style="height:10px"></div>
  </section>

</div>
</body>
</html>
```